Theatrical Producer/Consultant needs Artistic Brochure Shell and Inserts

Lanternfield Stageworks (www.lanternfieldstageworks.com) is a small company that offers theatrical producing and consulting services. We would like to create a brochure that contains information about our various productions and services. Because our roster is fluid, we are proposing to create a brochure shell or folder with pockets, and then a template for individual tear sheets that would be inserted into the inside pockets of the brochure shell/folder. The shell is intended for reuse each season, and new tear sheets will be developed separately on a project by project basis.
This task is to create the shell and a corresponding tear sheet template.
The brochure will be delivered by hand as well as by mail, so should fit into a standard size mailing envelope (i.e., within NPDS flat dimensions of 6 1/8" x 11 1/2")
The final design should reflect the high level of artistry of our theatrical projects. Attached are our logo as well as photos of current theatrical offerings which are available for use on the brochure shell but not required. There is also a file that describes our services in more detail, fyi. This will ultimately go onto one of the tear sheets in the brochure.
For the tear sheet template, we have also included a sample brochure from a peer colleague, just to give you an idea of the kind of information each sheet would contain. Each project page will contain title of the project, information about the artists involved, one or more photos, a project description, schedule, fee and other technical information.
The final files for both the shell and tear sheet templates should be printer-ready and also in a file format that we can edit ourselves in future.
Updates
Project Deadline Extended Reason: There was a discrepancy between posted project deadline (December 7) and when project was automatically closed (December 6). Since several designers who have not yet submitted indicated they were planning to submit designs, we wanted to make sure that they were able to do so. Added Monday, December 7, 2015
Industry/Entity Type
Performing Art
Font styles to use
Look and feel
Each slider illustrates characteristics of the customer's brand and the style your logo design should communicate.

```html
<!DOCTYPE html>
<html lang="en">
<head>
<meta charset="utf-8">
<title>Lanternfield Stageworks – Brochure Shell</title>
<link href="https://fonts.googleapis.com/css2?family=Lato:ital,wght@0,300;0,400;0,700;1,400&display=swap" rel="stylesheet">
<style>
  :root {
    --teal: #1aa3b8;
    --teal-deep: #0f8ea3;
    --teal-light: #7fd3df;
    --teal-pale: #dff3f6;
    --ink: #2c3a40;
    --white: #ffffff;
    --backdrop: #c9cbcc;
    --die-cut: #a9abac;
  }
  * { box-sizing: border-box; margin: 0; padding: 0; }
  html, body { width: 952px; height: 1200px; overflow: hidden; }
  body {
    background: var(--backdrop);
    font-family: "Lato", Arial, sans-serif;
    color: var(--ink);
    position: relative;
  }
  .spread {
    position: absolute;
    left: 76px;
    width: 800px;
    height: 555px;
    display: flex;
    box-shadow: 0 6px 18px rgba(0,0,0,.25);
  }
  .spread--outer { top: 30px; }
  .spread--inner { top: 615px; }
  .panel {
    position: relative;
    width: 400px;
    height: 100%;
    overflow: hidden;
  }

  /* Outer: back cover */
  .back-cover {
    background: linear-gradient(180deg, #ffffff 0%, var(--teal-pale) 30%, var(--teal-light) 62%, var(--teal) 100%);
  }
  .wordmark {
    position: absolute;
    display: flex;
    align-items: center;
    gap: 8px;
    font-weight: 700;
    letter-spacing: .3px;
  }
  .wordmark__dot { width: 20px; height: 20px; border-radius: 50%; }
  .back-cover .wordmark { left: 36px; top: 380px; color: var(--white); font-size: 21px; }
  .back-cover .wordmark__dot { background: var(--white); }
  .address {
    position: absolute; left: 46px; top: 424px;
    color: var(--white); font-style: italic; font-size: 14px; line-height: 1.5;
  }

  /* Outer: front cover */
  .front-cover {
    background: linear-gradient(180deg, #ffffff 0%, #f2fafb 28%, var(--teal-light) 62%, var(--teal) 100%);
  }
  .front-cover .wordmark { left: 22px; top: 26px; color: var(--teal-deep); font-size: 20px; }
  .front-cover .wordmark__dot { background: var(--teal-deep); }
  .die-cut {
    position: absolute; left: 62px; top: 100px;
    width: 180px; height: 180px; border-radius: 50%;
    background: var(--die-cut);
    box-shadow: inset 0 3px 8px rgba(0,0,0,.25), 0 0 0 2px var(--white);
  }
  .tagline {
    position: absolute; left: 22px; top: 330px; width: 320px;
    color: var(--white); font-weight: 300; font-size: 26px; line-height: 1.24;
  }
  .tagline strong { font-weight: 700; }

  /* Inner pages */
  .inner-left {
    background: linear-gradient(180deg, #ffffff 0%, #ffffff 55%, var(--teal-pale) 75%, var(--teal-light) 100%);
  }
  .inner-right {
    background: linear-gradient(180deg, #ffffff 0%, #ffffff 35%, var(--teal-light) 60%, var(--teal) 100%);
  }
  .photo {
    position: absolute; border-radius: 50%;
    border: 3px solid var(--teal);
  }
  .photo--dark { background: radial-gradient(circle at 45% 45%, #5b6470 0%, #23272d 60%, #0d0f12 100%); }
  .photo--night { background: radial-gradient(circle at 40% 35%, #e9ecef 0%, #5d6e66 25%, #1d2622 70%); }
  .photo--stage { background: radial-gradient(circle at 50% 45%, #b59a86 0%, #6b4a3e 40%, #161112 90%); }
  .photo--portrait { background: radial-gradient(circle at 55% 45%, #9aa2a8 0%, #4e5b66 50%, #1b2630 100%); }
  .photo--screen { background: radial-gradient(circle at 50% 50%, #3d4750 0%, #14181c 70%); border-color: var(--white); }

  .heading {
    position: absolute; color: var(--teal); font-size: 17px; font-weight: 400; line-height: 1.1;
  }
  .heading--white { color: var(--white); }
  .body-copy {
    position: absolute; font-size: 9.6px; line-height: 1.42; color: var(--ink);
  }
  .body-copy + .body-copy { margin-top: 0; }
  .body-copy .lead-word { color: var(--teal); font-size: 17px; }
  .body-copy--white { color: var(--white); font-style: italic; }
  .emphasis {
    position: absolute; font-style: italic; font-size: 9.6px; line-height: 1.42; color: var(--teal-deep);
  }
  .web {
    position: absolute; color: var(--white); font-size: 10.5px; letter-spacing: .3px;
  }
</style>
</head>
<body>

  <section class="spread spread--outer">
    <div class="panel back-cover">
      <div class="wordmark"><span class="wordmark__dot"></span>Lanternfield Stageworks</div>
      <p class="address">Lanternfield Stageworks<br>48 Wrenhollow Lane<br>Millbrook, NJ 08999</p>
    </div>

    <div class="panel front-cover">
      <div class="wordmark"><span class="wordmark__dot"></span>Lanternfield Stageworks</div>
      <div class="die-cut"></div>
      <h1 class="tagline">Dedicated to <strong>producing and consulting</strong> in the performing arts</h1>
    </div>
  </section>

  <section class="spread spread--inner">
    <div class="panel inner-left">
      <div class="photo photo--dark" style="left:34px;top:60px;width:112px;height:112px" role="img" aria-label="Photo: masked performers on a dark stage"></div>
      <h2 class="heading" style="left:162px;top:28px">Lanternfield<br>Stageworks LLC</h2>
      <p class="body-copy" style="left:162px;top:68px;width:210px">is a company dedicated to producing and consulting in the performing arts. From experimental to commercial, we collaborate with artists and organizations to foster an expansive range of compelling theatrical works for local, national and international audiences. We eschew boundaries—aesthetic, geopolitical, institutional—and thrive on a nimble and rigorous practice.</p>

      <div class="photo photo--night" style="left:252px;top:218px;width:104px;height:104px" role="img" aria-label="Photo: outdoor night performance under a large moon"></div>
      <p class="body-copy" style="left:34px;top:250px;width:200px"><span class="lead-word">As producers</span> we generate and develop our own innovative theatrical projects, serve as a creative producer for hire (by producing companies, independent artists and others) and provide other creative project-based services, including program development and dramaturgy.</p>

      <div class="photo photo--stage" style="left:44px;top:400px;width:114px;height:114px" role="img" aria-label="Photo: ensemble in costumes with raised arms"></div>
      <p class="body-copy" style="left:176px;top:385px;width:200px"><span class="lead-word">As consultants</span> we work with theater companies, presenters, performing arts centers, foundations and other non-profit or commercial entities to provide ongoing programming advice, research and development as well as broad policy, leadership and structural input and oversight</p>
    </div>

    <div class="panel inner-right">
      <div class="photo photo--portrait" style="left:32px;top:50px;width:118px;height:118px" role="img" aria-label="Photo: two performers in a close dramatic scene"></div>
      <p class="body-copy" style="left:168px;top:34px;width:206px">Our model of producing and consulting varies project-by-project, organization-by-organization. Our projects reflect a broad spectrum of genre, scale and clients. We examine the individual elements and/or artists involved and shape producing strategy around their particular visions.</p>
      <p class="body-copy" style="left:32px;top:192px;width:340px">By customizing an approach that capitalizes on the strengths of everyone involved and then identifying how to supplement those strengths we facilitate artistic excellence, while having a good time.</p>
      <p class="emphasis" style="left:32px;top:240px;width:340px">At its core, Lanternfield combines artistic values with an independent flexibility and financial structure that allow us to create a body of work that wouldn't exist under any other auspice.</p>

      <div class="photo photo--screen" style="left:236px;top:300px;width:124px;height:124px" role="img" aria-label="Photo: performer before a projected text backdrop"></div>
      <h2 class="heading heading--white" style="left:32px;top:306px;font-size:19px">Lanternfield<br>Stageworks LLC</h2>
      <p class="body-copy body-copy--white" style="left:32px;top:354px;width:190px">strives to be nimble, adaptive and clever, all qualities we bring to every stage we share.</p>
      <p class="web" style="left:32px;top:410px">www.lanternfieldstageworks.com</p>
    </div>
  </section>

</body>
</html>
```